kolvarin.link kolvarin.space kolvarin.press website

The website is named KOLVARIN and it will have 3 domain names. kolvarin.link, press, space.
I'd like it to be viewed on Pads, pcs and phones.

page menu:

kolvarin.link(start page): presentation of company. (creative, design, app, new product innovation.)
Here we'll need sosial media icons: plimber, vendoloop, mirtavel, trelvanet. (light but some 'fruity' colors)

kolvarin.press: blog. It will be a 75% picture blog > rest will be text. I need to be able to resize pictures and shape columns to picture size. (light but some 'fruity' colors)

kolvarin.space : the fun part of this web design, however, on entering the page I'd like a non-disclosure agreement where viewer simply click "yes, I agree" after filling out contact info. (check attached document)
We will have space here for uploading PDF files viewers can download. There is also a blog space here to tell in brief about the PDF file. (maybe a space/sci-fi theme her e.g spacechimp, Laika the space dog?)

I will attach the logo here I want you to use > and develop for the .space .press webpage. The logo i uploaded is for the .link page.

Target Market(s)

venture capitalists

Number of Pages Required

3 page

Requirements
Must have
• a few 'fruity colors' but mostly white and grey

```html
<!DOCTYPE html>
<html lang="en">
<head>
<meta charset="utf-8">
<title>Kolvarin</title>
<link href="https://fonts.googleapis.com/css2?family=Rajdhani:wght@500;600&family=Lato:wght@400;700&display=swap" rel="stylesheet">
<style>
:root{
  --red:#c95c50;
  --red-text:#d2493d;
  --green:#66ad5d;
  --green-dark:#4f9a47;
  --blue:#66a5cb;
  --purple:#8a56bf;
  --grey-top:#8f8f8f;
  --grey-strip:#bdbdbd;
  --page:#f3f3f3;
  --panel:#e9e9e9;
  --dark:#2c2c2c;
  --black:#151515;
  --ink:#333;
  --muted:#555;
  --white:#fff;
}
*{margin:0;padding:0;box-sizing:border-box}
html,body{width:915px;height:1200px;overflow:hidden}
body{position:relative;background:var(--page);font-family:'Lato',sans-serif;color:var(--ink)}
.abs{position:absolute}
.topbar{left:0;top:0;width:915px;height:31px;background:var(--grey-top)}
.navbar{left:0;top:31px;width:915px;height:35px;background:var(--red)}
.strip{left:0;top:66px;width:915px;height:7px;background:var(--grey-strip)}
.nav a{position:absolute;top:10px;color:var(--white);font-family:'Rajdhani',sans-serif;font-weight:500;font-size:12px;text-decoration:none}
.nav .sep{position:absolute;top:10px;width:1px;height:16px;background:rgba(255,255,255,.25)}
.nav .active::before,.nav .active::after{content:"";position:absolute;left:-7px;right:-7px;height:3px;background:var(--green)}
.nav .active::before{top:-10px}
.nav .active::after{top:21px}
.contact{top:6px;display:flex;align-items:center;gap:7px;color:var(--white);font-family:'Rajdhani',sans-serif;font-weight:500;font-size:12px}
.contact .ring{width:24px;height:24px;border:1.5px solid var(--white);border-radius:50%;display:flex;align-items:center;justify-content:center}
.logo{left:381px;top:-46px;width:154px;height:154px;border-radius:50%;background:var(--white);box-shadow:0 3px 8px rgba(0,0,0,.35);display:flex;align-items:flex-end;justify-content:center;padding-bottom:54px}
.logo span{font-family:'Rajdhani',sans-serif;font-weight:600;font-size:22px;letter-spacing:1px;color:var(--ink)}
.hero{left:0;top:73px;width:915px;height:357px;background:radial-gradient(ellipse at 22% 55%,#e9d27a 0%,#7c7a3f 14%,#1d2c45 38%,#0e1628 70%,#06080e 100%)}
.hero-art{left:230px;top:95px;width:560px;height:200px;background:radial-gradient(ellipse at 50% 50%,rgba(90,170,230,.45),rgba(200,80,160,.2) 45%,rgba(0,0,0,0) 70%)}
.caption{left:0;top:368px;width:915px;height:62px;background:rgba(0,0,0,.55)}
.caption h2{position:absolute;left:122px;top:14px;font-family:'Rajdhani',sans-serif;font-weight:500;font-size:25px;color:var(--white)}
.dots{position:absolute;left:757px;top:27px;display:flex;gap:4px}
.dots i{width:9px;height:9px;border-radius:50%;background:var(--white)}
.dots i:first-child{background:var(--red)}
.welcome{left:0;top:430px;width:915px;height:172px}
.welcome h1{position:absolute;left:0;width:915px;top:32px;text-align:center;font-family:'Rajdhani',sans-serif;font-weight:500;font-size:20px;color:#555}
.welcome h1 em{font-style:normal;color:var(--red-text)}
.welcome .rule{position:absolute;left:240px;top:64px;width:435px;height:6px;background:radial-gradient(ellipse at center,rgba(0,0,0,.12),rgba(0,0,0,0) 70%)}
.welcome p{position:absolute;left:122px;top:84px;width:671px;text-align:center;font-size:8.6px;line-height:14.6px;color:#444}
.welcome p a{color:var(--green);text-decoration:underline}
.features{left:0;top:602px;width:915px;height:232px;background:var(--panel)}
.card{position:absolute;top:67px;width:155px;height:113px;color:var(--white);text-align:center;font-family:'Rajdhani',sans-serif;font-weight:500;font-size:15px;line-height:17px}
.card .label{position:absolute;left:0;right:0;top:52px}
.card .badge{position:absolute;left:44px;top:-34px;width:67px;height:67px;border-radius:50%;background:var(--white);border:2px solid #eee;display:flex;align-items:center;justify-content:center}
.card .badge span{width:55px;height:55px;border-radius:50%;border:1.5px solid currentColor;display:flex;align-items:center;justify-content:center}
.card .plus{position:absolute;left:66px;top:101px;width:23px;height:23px;background:var(--dark);color:var(--white);font-family:'Lato',sans-serif;font-weight:700;font-size:16px;line-height:22px}
.creative{left:122px;background:var(--blue)}
.design{left:294px;background:var(--red)}
.app{left:465px;background:var(--green)}
.innovation{left:637px;background:var(--purple)}
.post{position:absolute;top:894px;width:323px;height:139px;background:var(--white);box-shadow:0 1px 3px rgba(0,0,0,.25)}
.post .photo{position:absolute;left:0;top:0;width:145px;height:139px}
.post h3{position:absolute;left:160px;top:14px;width:110px;font-size:9.5px;line-height:14px;font-weight:700;color:#111}
.post .line{position:absolute;left:157px;top:49px;width:155px;height:1px;background:#ddd}
.post p{position:absolute;left:157px;top:59px;width:158px;font-size:9px;line-height:14.5px;color:#444}
.post .more{position:absolute;left:158px;top:116px;font-size:7.5px;font-weight:700;color:var(--green);text-decoration:none}
.post .date{position:absolute;left:268px;top:-20px;width:42px;height:42px;background:var(--green);color:var(--white);text-align:center;box-shadow:0 1px 2px rgba(0,0,0,.2)}
.post .date b{display:block;font-family:'Rajdhani',sans-serif;font-weight:600;font-size:18px;line-height:20px;margin-top:3px}
.post .date small{display:block;font-size:8px;font-weight:700}
.footnav{left:0;top:1093px;width:915px;height:41px;background:var(--red);display:flex;justify-content:center;align-items:center;gap:14px;font-size:9.5px;color:var(--dark)}
.footnav .star{font-size:8px}
.footinfo{left:0;top:1134px;width:915px;height:38px;background:var(--dark);color:#ddd;font-size:8.5px}
.footinfo .item{position:absolute;top:11px;display:flex;align-items:center;gap:6px}
.subscribe{position:absolute;left:609px;top:6px;display:flex;align-items:center}
.subscribe .env{width:26px;height:26px;border-radius:50%;background:#ddd;display:flex;align-items:center;justify-content:center;margin-right:8px}
.subscribe .field{width:128px;height:20px;background:#222;color:#bbb;font-size:7.5px;padding:6px 7px}
.subscribe .go{width:23px;height:20px;background:var(--green);color:var(--white);font-family:'Rajdhani',sans-serif;font-weight:600;font-size:10px;text-align:center;line-height:20px}
.copyright{left:0;top:1172px;width:915px;height:28px;background:var(--black);color:var(--white);font-size:8px;font-weight:700}
.copyright p{position:absolute;left:124px;top:10px}
.social{position:absolute;left:705px;top:5px;display:flex;gap:5px}
.social i{width:18px;height:18px;border-radius:50%;background:var(--white)}
</style>
</head>
<body>

<header>
  <div class="abs topbar"></div>
  <div class="abs navbar">
    <nav class="nav">
      <a class="active" style="left:137px">Home</a>
      <span class="sep" style="left:184px"></span>
      <a style="left:205px">About</a>
      <span class="sep" style="left:252px"></span>
      <a style="left:272px">Press</a>
      <span class="sep" style="left:316px"></span>
      <a style="left:336px">Space</a>
    </nav>
    <div class="abs contact" style="left:555px">
      <span class="ring"><svg width="11" height="9" viewBox="0 0 11 9"><rect x="0.7" y="0.7" width="9.6" height="7.6" rx="1" fill="none" stroke="#fff" stroke-width="1.2"/><path d="M1 1.5l4.5 3.5 4.5-3.5" fill="none" stroke="#fff" stroke-width="1.2"/></svg></span>
      info@kolvarin.com
    </div>
    <div class="abs contact" style="left:684px">
      <span class="ring"><svg width="10" height="10" viewBox="0 0 10 10"><path d="M2 1l2 2-1 1.3c.6 1.2 1.5 2.1 2.7 2.7L6.9 6l2 2-1.2 1.4C4.6 9.2.8 5.4.6 2.3z" fill="#fff"/></svg></span>
      +1 234 5678 209
    </div>
  </div>
  <div class="abs strip"></div>
  <div class="abs logo"><span>KOLVARIN</span></div>
</header>

<section class="abs hero" role="img" aria-label="Hand holding a glowing tablet with colourful app icons flying out of it">
  <div class="abs hero-art" style="left:230px;top:22px"></div>
</section>
<div class="abs caption">
  <h2>Share your creativity to world</h2>
  <div class="dots"><i></i><i></i><i></i></div>
</div>

<section class="abs welcome">
  <h1>Welcome to <em>Brightmoor</em></h1>
  <div class="rule"></div>
  <p>Sed ut perspiciatis unde omnis iste natus error sit voluptatem accusantium doloremque laudantium, totam rem aperiam, eaque ipsa quae ab illo inventore veritatis et quasi architecto beatae vitae dicta sunt explicabo. Nemo enim ipsam voluptatem quia voluptas sit aspernatur aut odit aut voluptas sit aspernatur aut odit aut fugit. Sed ut perspiciatis unde omnis iste natus error sit voluptatem accusantium doloremque laudantium, totam rem aperiam, eaque ipsa quae ab illo inventore veritatis et quasi architecto beatae vitae dicta sunt explicabo. Nemo enim ipsam voluptatem quia voluptas sit aspernatur . <a>More</a></p>
</section>

<section class="abs features">
  <div class="card creative">
    <div class="badge" style="color:var(--blue)"><span>
      <svg width="30" height="30" viewBox="0 0 30 30"><path d="M8 27v-5c-3-2-4-5-4-8 0-6 5-11 11-11s10 4 10 9c0 2 2 4 2 5l-2 1v3c0 2-1 3-3 3h-2v3z" fill="#66a5cb"/><circle cx="13" cy="11" r="3" fill="#fff"/><circle cx="19" cy="16" r="2.2" fill="#fff"/></svg>
    </span></div>
    <div class="label">CREATIVE</div>
    <div class="plus">+</div>
  </div>
  <div class="card design">
    <div class="badge" style="color:var(--red)"><span>
      <svg width="30" height="30" viewBox="0 0 30 30" fill="none" stroke="#c95c50" stroke-width="1.8"><path d="M6 20L20 6l4 4-14 14H6z"/><path d="M7 6l17 17-3 3L4 9z"/></svg>
    </span></div>
    <div class="label">DESIGN</div>
    <div class="plus">+</div>
  </div>
  <div class="card app">
    <div class="badge" style="color:var(--green)"><span>
      <svg width="30" height="30" viewBox="0 0 30 30" fill="none" stroke="#66ad5d" stroke-width="1.8"><rect x="8" y="3" width="13" height="24" rx="2"/><circle cx="17" cy="14" r="4"/><circle cx="14.5" cy="23.5" r="1" fill="#66ad5d"/></svg>
    </span></div>
    <div class="label">APP</div>
    <div class="plus">+</div>
  </div>
  <div class="card innovation">
    <div class="badge" style="color:var(--purple)"><span>
      <svg width="30" height="30" viewBox="0 0 30 30" fill="none" stroke="#8a56bf" stroke-width="1.8"><path d="M10 17a6 6 0 1 1 10 0c-1 1.5-2 2.5-2 4h-6c0-1.5-1-2.5-2-4z"/><path d="M12 24h6M13 27h4M15 2v3M5 7l2 2M25 7l-2 2"/></svg>
    </span></div>
    <div class="label">NEW PRODUCT<br>INNOVATION</div>
    <div class="plus">+</div>
  </div>
</section>

<article class="post" style="left:123px">
  <div class="photo" role="img" aria-label="Tree painted with colourful paint splashes" style="background:radial-gradient(circle at 50% 38%,#e9697a 0%,#f3b546 22%,#7fb2e0 40%,#fff 62%)"></div>
  <h3>Simply dummy text of the printing</h3>
  <div class="line"></div>
  <p>Lorem Ipsum is simply dummy text of the printing and typesetting indus text ever since the 1500s,</p>
  <a class="more">Read More &gt;&gt;</a>
  <div class="date"><b>06</b><small>April</small></div>
</article>

<article class="post" style="left:469px">
  <div class="photo" role="img" aria-label="Crumpled yellow paper light bulb with the word Creative" style="background:radial-gradient(circle at 32% 50%,#f5de3a 0%,#f7ec9e 16%,#f4f4f0 38%,#e6e6e2 100%)"></div>
  <h3>Simply dummy text of the printing</h3>
  <div class="line"></div>
  <p>Lorem Ipsum is simply dummy text of the printing and typesetting indus text ever since the 1500s,</p>
  <a class="more">Read More &gt;&gt;</a>
  <div class="date"><b>04</b><small>April</small></div>
</article>

<footer>
  <nav class="abs footnav">
    <span>HOME</span><span class="star">★</span>
    <span>ABOUT US</span><span class="star">★</span>
    <span>PRESS</span><span class="star">★</span>
    <span>SPACE</span>
  </nav>
  <div class="abs footinfo">
    <div class="item" style="left:127px">
      <svg width="12" height="16" viewBox="0 0 12 16"><path d="M6 0a6 6 0 0 1 6 6c0 4-6 10-6 10S0 10 0 6a6 6 0 0 1 6-6z" fill="#ddd"/><circle cx="6" cy="6" r="2.3" fill="#2c2c2c"/></svg>
      Lorem ipsum dolor sit amet, adipiscing elit
    </div>
    <div class="item" style="left:347px;font-size:10px">
      <svg width="10" height="14" viewBox="0 0 10 14"><path d="M2 0l2.5 3-1.3 1.7c.5 2 1.5 3.7 3 4.7L8 8.3 10 11l-2 2.5C3 12 0 6 1 1z" fill="#ddd"/></svg>
      +1 234 5678 209
    </div>
    <div class="item" style="left:477px">
      <span style="font-size:17px;line-height:14px">@</span>
      info@kolvarin.com
    </div>
    <div class="subscribe">
      <span class="env"><svg width="13" height="10" viewBox="0 0 13 10"><rect width="13" height="10" rx="1.5" fill="#2c2c2c"/><path d="M1 1.5l5.5 4 5.5-4" fill="none" stroke="#ddd" stroke-width="1.2"/></svg></span>
      <span class="field">Enter Email</span>
      <span class="go">GO</span>
    </div>
  </div>
  <div class="abs copyright">
    <p>Copyright 2016  Kolvarin. All rights reserved.</p>
    <div class="social">
      <i title="mirtavel"></i><i title="plimber"></i><i title="vendoloop"></i><i title="trelvanet"></i>
    </div>
  </div>
</footer>

</body>
</html>
```